50's-style gig poster for a birthday bash

My wife was born in 1957 and is turning 57 next month. I'm throwing a surprise party for her, and thought it would be fun to have a 18x24 poster printed and framed for the event. Attached is a poster from a Rufus Kendrick gig in 1957. I'd like something like this, with a tinted B&W head shot of my wife, with similar fonts and background color schemes. The copy will be LORNA at the top (where the name RUFUS appears), with 57X57 under it, and the word Celebration where the word Quartet currently appears. The rest of the copy will be provided to you. Thanks for your interest and I look forward to working with you.

```html
<!DOCTYPE html>
<html lang="en">
<head>
<meta charset="utf-8">
<title>Lorna 57 x 57 Celebration</title>
<link href="https://fonts.googleapis.com/css2?family=Josefin+Sans:wght@700&family=Montserrat:ital,wght@0,700;1,500&family=Lobster&family=Arvo:wght@700&display=swap" rel="stylesheet">
<style>
  :root {
    --paper: #e6d7b3;
    --blue: #1f4595;
    --red: #e2212b;
    --cream: #f1e9d6;
    --ink: #1a1a1f;
    --navy: #1f3a86;
    --photo-dark: #5d5d5d;
    --photo-light: #cfcfcf;
  }
  * { margin: 0; padding: 0; box-sizing: border-box; }
  html, body { width: 834px; height: 1200px; overflow: hidden; background: var(--paper); }
  .poster { position: relative; width: 834px; height: 1200px; background: var(--paper); overflow: hidden; }
  .stripe { position: absolute; top: 19px; height: 1161px; width: 136px; }
  .stripe--blue { background: var(--blue); }
  .stripe--red { background: var(--red); }

  .headline-letter, .headline-digit {
    position: absolute; width: 136px; text-align: center;
    font-family: "Josefin Sans", "Futura", sans-serif; font-weight: 700;
    color: var(--cream); text-shadow: 5px 5px 0 var(--ink);
    line-height: 1;
  }
  .headline-letter { top: 34px; font-size: 150px; }
  .headline-digit { top: 178px; font-size: 150px; }
  .headline-times { top: 222px; font-size: 96px; }

  .portrait {
    position: absolute; left: 62px; top: 360px; width: 340px; height: 410px;
    transform: rotate(-3deg);
    border: 3px solid var(--ink);
    background: linear-gradient(160deg, var(--photo-light), var(--photo-dark));
  }

  .celebration {
    position: absolute; left: 400px; top: 340px; width: 370px; text-align: center;
    font-family: "Lobster", cursive; font-size: 64px; color: var(--cream);
    text-shadow: 4px 4px 0 var(--ink); transform: rotate(-5deg);
  }
  .lineup { position: absolute; left: 400px; top: 452px; width: 334px; text-align: center; color: var(--cream); }
  .lineup__label { font-family: "Montserrat", sans-serif; font-style: italic; font-weight: 500; font-size: 25px; text-shadow: 2px 2px 0 var(--ink); }
  .lineup__act { font-family: "Montserrat", sans-serif; font-weight: 700; font-size: 23px; line-height: 38px; text-shadow: 2px 2px 0 var(--ink); white-space: nowrap; }

  .date-badge { position: absolute; left: 505px; top: 737px; width: 200px; height: 142px; }
  .date-badge__text { position: absolute; left: 0; top: 0; width: 200px; text-align: center; color: var(--navy); }
  .date-badge__title { font-family: "Arvo", serif; font-weight: 700; font-size: 29px; line-height: 32px; margin-top: 18px; }
  .date-badge__when { font-family: "Montserrat", sans-serif; font-weight: 700; font-size: 17px; line-height: 24px; margin-top: 6px; }

  .also-tag {
    position: absolute; left: 128px; top: 865px; width: 246px; height: 39px;
    background: var(--cream); border: 2px solid var(--ink);
    font-family: "Montserrat", sans-serif; font-weight: 700; font-size: 22px;
    color: var(--navy); text-align: center; line-height: 35px;
  }
  .support-act {
    position: absolute; left: 0; top: 925px; width: 834px; text-align: center;
    font-family: "Lobster", cursive; font-size: 70px; color: var(--cream);
    text-shadow: 4px 4px 0 var(--ink); white-space: nowrap;
  }

  .venue {
    position: absolute; left: 65px; top: 1030px; width: 703px; height: 116px;
    background: var(--cream); border: 3px solid var(--ink); text-align: center;
  }
  .venue__name { font-family: "Arvo", serif; font-weight: 700; font-size: 58px; letter-spacing: 5px; color: var(--ink); line-height: 62px; margin-top: 6px; }
  .venue__address { font-family: "Montserrat", sans-serif; font-weight: 700; font-size: 21px; letter-spacing: 2px; color: var(--navy); line-height: 36px; }
</style>
</head>
<body>
<main class="poster">
  <div class="stripe stripe--blue" style="left:34px"></div>
  <div class="stripe stripe--red" style="left:190px"></div>
  <div class="stripe stripe--blue" style="left:347px"></div>
  <div class="stripe stripe--red" style="left:502px"></div>
  <div class="stripe stripe--blue" style="left:659px"></div>

  <h1 aria-label="LORNA">
    <span class="headline-letter" style="left:34px">L</span>
    <span class="headline-letter" style="left:190px">O</span>
    <span class="headline-letter" style="left:347px">R</span>
    <span class="headline-letter" style="left:502px">N</span>
    <span class="headline-letter" style="left:659px">A</span>
  </h1>
  <div aria-label="57 x 57">
    <span class="headline-digit" style="left:34px">5</span>
    <span class="headline-digit" style="left:190px">7</span>
    <span class="headline-digit headline-times" style="left:347px">x</span>
    <span class="headline-digit" style="left:502px">5</span>
    <span class="headline-digit" style="left:659px">7</span>
  </div>

  <div class="portrait" role="img" aria-label="Black and white portrait photo of Lorna"></div>

  <div class="celebration">Celebration</div>
  <div class="lineup">
    <div class="lineup__label">Featuring:</div>
    <div class="lineup__act">The Marlowes</div>
    <div class="lineup__act">The Brightwaters</div>
    <div class="lineup__act">The Penrose-Ashbys</div>
    <div class="lineup__act">The Fairbanks</div>
    <div class="lineup__act">The Tollivers</div>
    <div class="lineup__act">TheDelacroixs</div>
  </div>

  <div class="date-badge">
    <svg width="200" height="142" viewBox="0 0 200 142">
      <ellipse cx="100" cy="71" rx="98" ry="69" fill="var(--cream)" stroke="var(--ink)" stroke-width="2.5"/>
    </svg>
    <div class="date-badge__text">
      <div class="date-badge__title">One Night<br>Only</div>
      <div class="date-badge__when">April 4, 2014<br>6 PM</div>
    </div>
  </div>

  <div class="also-tag">Also Appearing</div>
  <div class="support-act">The Chirps &amp; Gil Tovar</div>

  <div class="venue">
    <div class="venue__name">BISTRO MARCEL</div>
    <div class="venue__address">818 Cedar Street, Paso Robles, California</div>
  </div>
</main>
</body>
</html>
```